Motivational Poster Design Project

I would like to create a poster with some of my favorite quotes to hang in my office. I did a similar project in 2012 and I've uploaded the top 2 designs so you can get a better idea of what I'm looking for. I will provide feedback on your design within 24 hours of receiving it.

The poster must contain the following quotes:

"You’re only given a little spark of madness. You mustn’t lose it.”
- Dorian Fletcher

“The most contrarian thing of all is not to oppose the crowd but to think for yourself.”
- Marcus Olden

"I constantly see people rise in life who are not the smartest, sometimes not even the most diligent, but they are learning machines. They go to bed every night a little wiser than they were when they got up and boy does that help, particularly when you have a long run ahead of you."
- Frankie Dalgarth

“In theory, there’s no difference between theory and practice. But, in practice, there is.”
- Kees R. T. Ter Haverkamp

"At the end of the day, a reactionary life is a normal life. One thing is consistent in every remarkable person: they decide to do something remarkable. Don’t let the world choose who you become."
- Rohan Kapadia

“It usually takes 3-4 months to try enough that you can do a proper 80/20 analysis, then two months to design systems to scale what *is* working.”
-Ned Yarrow

“Authority is 20 percent given, 80 percent taken.”
- Glenn Mosbacker

“Your actions are consistent with the way the world occurs to you.”
- Dieter Kolbach

Project Deadline Extended
Reason: I am going to be travelling with no access to internet until January 5th, 2015. I am extending the project deadline until 12/31/14 and I'll make a final decision during the 1st week of January.

Target Market(s)

Personal Project

Industry/Entity Type

Learning

Requirements
Must have
• The poster will be 24" high x 36" long and printed on canvas, so the image you create needs to have a resolution of at least 2700 x 3900.
Nice to have
• I don't have an exact vision for how the poster should look, so I am totally open to you using your creativity to develop, arrange and present the content as you'd like.
• That said, I would like an image (photo or posterized image) of the person being quoted along with each quote. I do not have specific images that I would like you to use, so you will need to find the images on your own. The images don't need to be perfect... I am more interested in the poster relating the essence of the quotes and the people being quoted than I am in perfect photographic images of the people being quoted.

```html
<!DOCTYPE html>
<html lang="en">
<head>
<meta charset="utf-8">
<title>Learning Quotes Poster</title>
<link href="https://fonts.googleapis.com/css2?family=Cabin+Condensed:wght@400;500;600&family=Open+Sans:wght@800&display=swap" rel="stylesheet">
<style>
:root{
  --board:#1b1b1b;
  --board-light:#2a2a2a;
  --chalk:#f1f1f1;
  --frame-line:#d6d6d6;
  --numeral:#4a4a4a;
  --pink:#f3a9c6;
  --blue:#7fcaf2;
  --yellow:#f2e27a;
  --mint:#b8e6a8;
  --lime:#c9ea6c;
  --lavender:#bbb5e8;
  --photo-light:#8a8a8a;
  --photo-mid:#4a4a4a;
}
*{margin:0;padding:0;box-sizing:border-box}
html,body{width:1200px;height:800px;overflow:hidden;background:var(--board)}
.poster{
  position:relative;width:1200px;height:800px;overflow:hidden;
  background:radial-gradient(ellipse at 50% 45%,var(--board-light) 0%,var(--board) 78%);
  font-family:"Cabin Condensed",sans-serif;color:var(--chalk);
}
.chalk-sticks{position:absolute;left:114px;top:0;width:162px;height:126px;border-radius:0 0 24px 24px;
  background:linear-gradient(90deg,#e9cf4a 0 20%,#a98ad6 20% 40%,#e15d8c 40% 60%,#8fcf6a 60% 80%,#5fb0e6 80%);opacity:.45}
.corner-ornament{position:absolute;width:56px;height:56px;border-radius:50%;background:#9a9a9a;opacity:.12}
.portrait{position:absolute;border-radius:50%;
  background:radial-gradient(circle,var(--photo-light) 0%,var(--photo-mid) 40%,rgba(27,27,27,0) 70%)}
.doodle{position:absolute;border-radius:50%;background:#a0a0a0;opacity:.22}
.art{position:absolute;left:0;top:0}
.numeral{font-family:"Open Sans",sans-serif;font-weight:800;fill:var(--numeral)}
.txt{position:absolute;white-space:nowrap;font-size:14.5px;line-height:24px;font-weight:500}
.txt .em{font-size:20px}
.small{font-size:13px}
.small .em{font-size:18px}
.author{position:absolute;white-space:nowrap;font-size:15.5px;line-height:24px;font-weight:500}
.inline-author{font-size:15.5px}
.pink{color:var(--pink)} .blue{color:var(--blue)} .yellow{color:var(--yellow)}
.mint{color:var(--mint)} .lime{color:var(--lime)} .lavender{color:var(--lavender)}
</style>
</head>
<body>
<main class="poster">
  <div class="portrait" style="left:72px;top:192px;width:156px;height:156px" role="img" aria-label="Black and white portrait of Dorian Fletcher"></div>
  <div class="portrait" style="left:400px;top:118px;width:148px;height:148px" role="img" aria-label="Black and white photo of Marcus Olden speaking"></div>
  <div class="portrait" style="left:582px;top:356px;width:116px;height:116px" role="img" aria-label="Black and white portrait of Frankie Dalgarth"></div>
  <div class="portrait" style="left:936px;top:98px;width:156px;height:156px" role="img" aria-label="Black and white portrait of Kees R. T. Ter Haverkamp"></div>
  <div class="portrait" style="left:62px;top:434px;width:140px;height:140px" role="img" aria-label="Black and white portrait of Rohan Kapadia"></div>
  <div class="portrait" style="left:312px;top:560px;width:150px;height:150px" role="img" aria-label="Black and white portrait of Ned Yarrow smiling"></div>
  <div class="portrait" style="left:662px;top:528px;width:166px;height:166px" role="img" aria-label="Black and white portrait of Glenn Mosbacker"></div>
  <div class="portrait" style="left:956px;top:338px;width:140px;height:140px" role="img" aria-label="Black and white photo of Dieter Kolbach in a light suit"></div>

  <svg class="art" width="1200" height="800" viewBox="0 0 1200 800">
    <rect x="38" y="38" width="1124" height="724" rx="30" fill="none" stroke="var(--frame-line)" stroke-width="2.5" opacity=".85"/>
    <rect x="47" y="47" width="1106" height="706" rx="24" fill="none" stroke="var(--frame-line)" stroke-width="1" opacity=".55"/>
    <text class="numeral" x="290" y="264" font-size="112">1</text>
    <text class="numeral" x="796" y="186" font-size="112">2</text>
    <text class="numeral" x="806" y="432" font-size="100">3</text>
    <text class="numeral" x="1074" y="228" font-size="100">4</text>
    <text class="numeral" x="224" y="660" font-size="112">5</text>
    <text class="numeral" x="528" y="594" font-size="112">6</text>
    <text class="numeral" x="846" y="630" font-size="100">7</text>
    <text class="numeral" x="1086" y="432" font-size="80">8</text>
    <polyline points="780,474 800,460 814,466 830,446 844,448" fill="none" stroke="var(--yellow)" stroke-width="2"/>
    <polyline points="832,436 846,438 842,452" fill="none" stroke="var(--yellow)" stroke-width="2"/>
    <polyline points="448,526 448,576 504,576" fill="none" stroke="var(--yellow)" stroke-width="1.5"/>
    <polyline points="452,566 466,550 478,558 490,540 502,546" fill="none" stroke="var(--yellow)" stroke-width="1.5"/>
    <polyline points="452,570 468,560 480,564 494,552 504,556" fill="none" stroke="var(--lime)" stroke-width="1.5"/>
  </svg>

  <div class="chalk-sticks" role="img" aria-label="Five coloured chalk sticks hanging from the top edge"></div>
  <div class="corner-ornament" style="left:26px;top:26px" role="img" aria-label="Leaf corner ornament"></div>
  <div class="corner-ornament" style="right:26px;top:26px" role="img" aria-label="Leaf corner ornament"></div>
  <div class="corner-ornament" style="left:26px;bottom:26px" role="img" aria-label="Leaf corner ornament"></div>
  <div class="corner-ornament" style="right:26px;bottom:26px" role="img" aria-label="Leaf corner ornament"></div>

  <div class="doodle" style="left:252px;top:218px;width:28px;height:40px" role="img" aria-label="Chalk light bulb doodle"></div>
  <div class="doodle" style="left:790px;top:194px;width:46px;height:36px" role="img" aria-label="Chalk doodle of two figures with speech bubbles"></div>
  <div class="doodle" style="left:1084px;top:242px;width:28px;height:24px;border-radius:3px" role="img" aria-label="Chalk eraser doodle"></div>
  <div class="doodle" style="left:180px;top:570px;width:38px;height:38px" role="img" aria-label="Chalk globe doodle"></div>
  <div class="doodle" style="left:1044px;top:552px;width:40px;height:40px" role="img" aria-label="Chalk compass rose doodle"></div>
  <div class="doodle" style="left:962px;top:638px;width:30px;height:50px;border-radius:4px" role="img" aria-label="Chalk pencil doodle"></div>

  <!-- Quote 1 -->
  <div class="txt" style="left:204px;top:271px">“You’re only given a</div>
  <div class="txt" style="left:204px;top:296px">little <span class="em">spark</span> of madness.</div>
  <div class="txt" style="left:204px;top:320px">You mustn’t <span class="em">lose</span> it.”</div>
  <div class="author pink" style="left:206px;top:346px">- Dorian Fletcher</div>

  <!-- Quote 2 -->
  <div class="txt" style="left:546px;top:146px">“The most <span class="em">contrarian</span> thing of all is</div>
  <div class="txt" style="left:546px;top:172px">not to oppose the crowd but <span class="em">to think</span></div>
  <div class="txt" style="left:546px;top:197px"><span class="em">for yourself</span>.” <span class="inline-author blue">- Marcus Olden</span></div>

  <!-- Quote 3 -->
  <div class="txt small" style="left:442px;top:318px">“I constantly see people rise in life who are not the <span class="em">smartest</span>, sometimes</div>
  <div class="txt small" style="left:442px;top:343px">not even the most <span class="em">diligent</span>, but</div>
  <div class="txt small" style="left:690px;top:343px">they are <span class="em">learning</span></div>
  <div class="txt small" style="left:442px;top:368px"><span class="em">machines</span>. They go to bed</div>
  <div class="txt small" style="left:704px;top:368px">every night a little</div>
  <div class="txt small" style="left:442px;top:393px"><span class="em">wiser</span> than they were when</div>
  <div class="txt small" style="left:709px;top:393px">they got up and boy</div>
  <div class="txt small" style="left:442px;top:418px">does that help, particularly</div>
  <div class="txt small" style="left:702px;top:418px">when you have a</div>
  <div class="txt small" style="left:442px;top:440px"><span class="em">long run</span> ahead of you.”</div>
  <div class="author yellow" style="left:690px;top:436px">- Frankie Dalgarth</div>

  <!-- Quote 4 -->
  <div class="txt" style="left:894px;top:246px"><span class="em">“In theory</span>, there’s no between</div>
  <div class="txt" style="left:894px;top:274px">theory and practice. But, <span class="em">in practice</span>,</div>
  <div class="txt" style="left:894px;top:298px">there is.” <span class="inline-author mint">- Kees R. T. Ter Haverkamp</span></div>

  <!-- Quote 5 -->
  <div class="txt small" style="left:74px;top:410px">“At the end of the day, a reactionary life is a <span class="em">normal life</span>.</div>
  <div class="txt small" style="left:204px;top:433px">One thing is consistent in every</div>
  <div class="txt small" style="left:222px;top:457px"><span class="em">remarkable person</span>:</div>
  <div class="txt small" style="left:222px;top:479px">they decide to do something remarkable.</div>
  <div class="txt small" style="left:216px;top:500px"><span class="em">Don’t let the world choose</span></div>
  <div class="txt small" style="left:216px;top:523px"><span class="em">who you become</span>.”</div>
  <div class="author pink" style="left:214px;top:545px">- Rohan Kapadia</div>

  <!-- Quote 6 -->
  <div class="txt small" style="left:462px;top:582px">“It usually takes <span class="em">3-4 months</span></div>
  <div class="txt small" style="left:462px;top:607px">to try enough that you can do a proper</div>
  <div class="txt small" style="left:462px;top:627px">80/20 analysis, then <span class="em">two months</span></div>
  <div class="txt small" style="left:462px;top:649px">to design systems to scale</div>
  <div class="txt small" style="left:462px;top:669px"><span class="em">what *is* working</span>.”</div>
  <div class="author lime" style="left:462px;top:688px">- Ned Yarrow</div>

  <!-- Quote 7 -->
  <div class="txt" style="left:834px;top:612px">“Authority is <span class="em">20 percent given</span>,</div>
  <div class="txt" style="left:834px;top:636px"><span class="em">80 percent taken</span>.”</div>
  <div class="author pink" style="left:834px;top:658px">- Glenn Mosbacker</div>

  <!-- Quote 8 -->
  <div class="txt" style="left:932px;top:496px">“Your <span class="em">actions</span> are <span class="em">consistent</span></div>
  <div class="txt" style="left:932px;top:518px">with the way the world occurs to you.”</div>
  <div class="author lavender" style="left:932px;top:540px">- Dieter Kolbach</div>
</main>
</body>
</html>
```